Business Card Design for a Personal Trainer

I need a business card design for my job as a personal trainer. It should have a unique, modern and exclusive design. On the front there should be only my logo with my name and my job. 0162/3819204 Tobias Lendhart Wiesengrundweg 14 80417 Munich Germany The most important contact information is the web adress. it can be bigger than the rest, but its not necessary. The card should be 8,5cmx5,5cm big. Font: Roboto. Colors: black, white, gray, 56c1ff.

```html
<!DOCTYPE html>
<html lang="de">
<head>
<meta charset="utf-8">
<title>Tobias Lendhart – Personal Trainer Visitenkarte</title>
<link rel="stylesheet" href="https://fonts.googleapis.com/css2?family=Roboto:wght@300;400;500&family=Libre+Baskerville:wght@400&display=swap">
<style>
  :root {
    --stage: #1c1a1d;
    --card-dark: #6f6f6f;
    --card-mid: #b4b4b4;
    --card-light: #f7f7f7;
    --ink: #111111;
    --text: #1a1a1a;
    --accent: #c2185b;
    --photo-dark: #3a3a3a;
    --photo-light: #8a8a8a;
  }
  html, body {
    margin: 0;
    padding: 0;
    width: 1200px;
    height: 969px;
    overflow: hidden;
    background: var(--stage);
  }
  .card {
    position: absolute;
    left: 50px;
    top: 154px;
    width: 1100px;
    height: 660px;
    overflow: hidden;
    background: linear-gradient(115deg, var(--card-dark) 0%, var(--card-mid) 45%, var(--card-light) 85%, #ffffff 100%);
    font-family: "Roboto", sans-serif;
    color: var(--text);
  }
  .trainer-photo {
    position: absolute;
    left: 40px;
    top: 45px;
    width: 345px;
    height: 615px;
    background: linear-gradient(180deg, var(--photo-light) 0%, var(--photo-dark) 45%, #2b2b2b 100%);
    border-radius: 140px 140px 0 0;
  }
  .brand {
    position: absolute;
    left: 480px;
    width: 470px;
    top: 60px;
    text-align: center;
  }
  .brand-mark {
    display: block;
    width: 70px;
    height: 70px;
    margin: 40px auto 38px;
    background: var(--ink);
  }
  .brand-name {
    font-size: 47px;
    font-weight: 400;
    color: var(--ink);
    letter-spacing: 0.5px;
    line-height: 1;
    white-space: nowrap;
  }
  .brand-role {
    display: flex;
    align-items: center;
    justify-content: center;
    gap: 6px;
    margin-top: 6px;
    font-size: 19px;
    letter-spacing: 4px;
    color: var(--ink);
  }
  .brand-role .rule {
    display: block;
    width: 58px;
    height: 2px;
    background: var(--ink);
  }
  .contact {
    position: absolute;
    left: 380px;
    width: 670px;
    top: 330px;
    text-align: center;
  }
  .contact-name {
    font-family: "Libre Baskerville", serif;
    font-size: 33px;
    letter-spacing: 1px;
    color: var(--ink);
    margin: 0;
  }
  .contact-web {
    font-size: 33px;
    font-weight: 300;
    letter-spacing: 1px;
    color: var(--accent);
    margin: 22px 0 0;
  }
  .contact-line {
    font-size: 27px;
    letter-spacing: 1px;
    margin: 0;
    line-height: 42px;
  }
  .contact-phone { margin-top: 28px; }
</style>
</head>
<body>
  <div class="card">
    <div class="trainer-photo" role="img" aria-label="Schwarz-Weiß-Porträt des Trainers mit verschränkten Armen"></div>

    <div class="brand">
      <span class="brand-mark"></span>
      <div class="brand-name">TOBIAS LENDHART</div>
      <div class="brand-role"><span class="rule"></span>PERSONAL TRAINER<span class="rule"></span></div>
    </div>

    <div class="contact">
      <p class="contact-name">Tobias Lendhart</p>
      <p class="contact-web">www.tobiaslendhart.de</p>
      <p class="contact-line contact-phone">0162/3819204</p>
      <p class="contact-line">t.lendhart@postfach.de</p>
      <p class="contact-line">Wiesengrundweg 14,80417 München</p>
    </div>
  </div>
</body>
</html>
```